School Website

I need a design for a School (2 sections: Primary 6-12 years and Secondary 12-18 years). The first page is just a choice of the 2 sections. After we'll need 2 websites (with the same structure: Menu, ...) but with different colors. In fact, we need for end of October, 6 design of school website. So the best websites are going to be made available to you in the future (in pixelharbor) but privately.

Target Market(s)

Public, Parents, ...

Coding

Coded - Design and coding required

Number of Pages Required

5+ page

Font styles to use
Sans Serif

Colors
34a6d7
85cae6
cee9f5
ffffff

Requirements
Must have
• You can check the old Website: http: / /velmot.be We need the same pages with the same content. Menu: - HomePage - News and communication (like blog page) - Activities (like blog page, with photo gallery) - Contact (Contact form + maps) - In the main menu, we need a special button to connect to an external Website ( button needs to be different than the other menu items The name of this button is "Parents Area"). The logo of 2 sections are attached. Please use it for the design and the choice of colors.
Nice to have
• This is a web design of other school that we like: https://www.quintelo.be

```html
<!DOCTYPE html>
<html lang="fr">
<head>
<meta charset="utf-8">
<title>Lycée Royal de Velmont – Maternelles et Primaires</title>
<link href="https://fonts.googleapis.com/css2?family=Roboto:wght@400;500;700&family=Poppins:wght@400;500&display=swap" rel="stylesheet">
<style>
:root{
  --navy:#0b3f7f;
  --orange:#f4a81c;
  --ink:#1f2a36;
  --muted:#7a7f86;
  --card:#f4f4f4;
  --footer:#f7f7f7;
  --white:#ffffff;
}
*{margin:0;padding:0;box-sizing:border-box}
html,body{width:1200px;height:3465px;overflow:hidden}
body{position:relative;font-family:"Roboto",sans-serif;color:var(--ink);background:var(--white)}
a{text-decoration:none}
.abs{position:absolute}
.topbar{left:0;top:0;width:1200px;height:43px;background:var(--navy);color:var(--white);font-size:14.5px}
.topbar .item{position:absolute;top:13px;display:flex;align-items:center;gap:10px;white-space:nowrap}
.topbar svg{width:13px;height:13px}
.header{left:0;top:43px;width:1200px;height:89px;background:var(--white)}
.brand{position:absolute;left:89px;top:30px;display:flex;align-items:center;gap:10px;font:700 21px "Roboto",sans-serif;color:var(--navy);white-space:nowrap}
.brand .mark{width:20px;height:20px;background:var(--orange)}
.menu-bar{position:absolute;right:94px;top:34px;display:flex;gap:28px;font-size:14px;font-weight:500;color:var(--ink);white-space:nowrap}
.menu-bar .active{color:var(--navy)}
.hero{left:0;top:132px;width:1200px;height:562px;background:linear-gradient(115deg,#4f6270 0%,#7d8a86 18%,#b08f78 38%,#c89f84 52%,#9a8a84 68%,#6e8aa6 82%,#cfd2d4 100%)}
.hero-shade{left:0;top:132px;width:1200px;height:562px;background:rgba(20,30,45,.18)}
.hero-title{left:0;top:322px;width:1200px;text-align:center;color:var(--white);font-size:66px;font-weight:500;line-height:76px;text-shadow:0 2px 8px rgba(0,0,0,.35)}
.hero-sub{left:0;top:400px;width:1200px;text-align:center;color:var(--white);font-size:44px;font-weight:700;line-height:52px;text-shadow:0 2px 8px rgba(0,0,0,.35)}
.btn{position:absolute;display:flex;align-items:center;justify-content:center;color:var(--white);font-weight:500;font-size:15.5px;white-space:nowrap}
.btn.navy{background:var(--navy)}
.btn.orange{background:var(--orange)}
.card{position:absolute;top:769px;width:310px;height:330px;background:var(--card);text-align:center}
.card svg{margin-top:38px;width:86px;height:86px}
.card h3{font-size:25px;font-weight:400;margin-top:14px;color:var(--ink)}
.card p{font-size:14.5px;line-height:19.6px;color:var(--muted);margin:12px 16px 0}
.card .more{display:block;margin-top:12px;color:var(--navy);font-size:15.5px;font-weight:500}
.section-title{left:0;top:1164px;width:1200px;text-align:center;font-size:40px;font-weight:500;color:var(--navy)}
.rule{height:3px;background:var(--orange)}
.photo{position:absolute}
.post-img{position:absolute;top:1259px;width:475px;height:291px;border-radius:6px}
.arrow-btn{position:absolute;top:1532px;width:52px;height:35px;border-radius:18px;background:var(--white);box-shadow:0 2px 8px rgba(0,0,0,.12);display:flex;align-items:center;justify-content:center}
.post-date{position:absolute;top:1574px;font-size:21px;font-weight:500;color:var(--ink)}
.post-text{position:absolute;top:1612px;width:300px;font-size:14.5px;line-height:20.5px;color:var(--muted)}
.map{left:0;top:2603px;width:597px;height:555px;background:linear-gradient(160deg,#e9e8e4 0%,#dedcd6 40%,#c4dbe9 62%,#dfe4e2 78%,#e6e4df 100%)}
.contact{left:597px;top:2603px;width:603px;height:555px;background:var(--navy);color:var(--white)}
.contact h2{position:absolute;left:66px;top:82px;font-size:37px;font-weight:500}
.field{position:absolute;border-bottom:1px solid rgba(255,255,255,.35);font-size:14.5px;padding-bottom:8px}
.footer{left:0;top:3158px;width:1200px;height:307px;background:var(--footer);font-family:"Poppins",sans-serif}
.footer-brand{position:absolute;left:90px;top:70px;display:flex;align-items:center;gap:8px;font:500 16px "Poppins",sans-serif;color:var(--navy);white-space:nowrap}
.footer-brand .mark{width:16px;height:16px;background:var(--orange)}
.flink{position:absolute;font-size:14.5px;color:#8a8f96;white-space:nowrap}
.social{position:absolute;top:3431px;width:12px;height:12px;border-radius:50%;background:var(--navy)}
</style>
</head>
<body>

<div class="abs topbar">
  <div class="item" style="left:91px">
    <svg viewBox="0 0 24 24"><path fill="#fff" d="M6.6 10.8a15.1 15.1 0 0 0 6.6 6.6l2.2-2.2a1 1 0 0 1 1-.25 11.4 11.4 0 0 0 3.6.57 1 1 0 0 1 1 1V20a1 1 0 0 1-1 1A17 17 0 0 1 3 4a1 1 0 0 1 1-1h3.5a1 1 0 0 1 1 1c0 1.25.2 2.45.57 3.57a1 1 0 0 1-.25 1z"/></svg>
    <span>+32 81 40 55 12</span>
  </div>
  <div class="item" style="left:233px">
    <svg viewBox="0 0 24 24"><path fill="#fff" d="M12 2a7 7 0 0 0-7 7c0 5.25 7 13 7 13s7-7.75 7-13a7 7 0 0 0-7-7zm0 9.5A2.5 2.5 0 1 1 12 6.5a2.5 2.5 0 0 1 0 5z"/></svg>
    <span>Rue des Tilleuls 14, 5000 Velmont, Belgique</span>
  </div>
  <div class="item" style="left:557px">
    <svg viewBox="0 0 24 24"><circle cx="12" cy="12" r="9.5" fill="none" stroke="#fff" stroke-width="2.4"/><path d="M12 7v5l3 2" fill="none" stroke="#fff" stroke-width="2.4"/></svg>
    <span>Du lundi au vendredi 7h00 – 18h</span>
  </div>
</div>

<header class="abs header">
  <div class="brand"><span class="mark"></span>Lycée Royal de Velmont</div>
  <nav class="menu-bar">
    <span class="active">Accueil</span>
    <span>Secondaire</span>
    <span>Lycée Royal de Velmont</span>
    <span>Contact</span>
    <span>Plan</span>
  </nav>
</header>

<section class="abs hero" role="img" aria-label="Photo of a teacher and young pupils gathered around a table in a classroom"></section>
<div class="abs hero-shade"></div>
<h1 class="abs hero-title">Lycée Royal de Velmont</h1>
<p class="abs hero-sub">Maternelles et Primaires</p>
<a class="btn navy" style="left:444px;top:475px;width:151px;height:41px">Parents Area</a>
<a class="btn orange" style="left:604px;top:475px;width:153px;height:41px">Communications</a>

<div class="card" style="left:86px">
  <svg viewBox="0 0 64 64" fill="none" stroke="#1f2a36" stroke-width="2"><path d="M32 4v8M32 4h7v4h-7"/><path d="M20 22l12-10 12 10"/><rect x="20" y="22" width="24" height="36"/><rect x="6" y="32" width="14" height="26"/><rect x="44" y="32" width="14" height="26"/><rect x="28" y="46" width="8" height="12"/><rect x="25" y="28" width="5" height="5"/><rect x="34" y="28" width="5" height="5"/><rect x="25" y="37" width="5" height="5"/><rect x="34" y="37" width="5" height="5"/><rect x="10" y="38" width="6" height="6"/><rect x="48" y="38" width="6" height="6"/><path d="M2 58h60"/><path d="M9 50c0-4 4-4 4 0v8" stroke="#f4a81c"/></svg>
  <h3>School Holidays</h3>
  <p>L’établissement sera ouvert jusqu’au 5 juillet 2018 inclus et à partir du 16 août 2018 de 9h à 15h. Rentrée scolaire : lundi 3 septembre&nbsp; Fête de la Communau française : jeudi 27 septembre</p>
  <span class="more">Read More</span>
</div>
<div class="card" style="left:438px;top:767px">
  <svg viewBox="0 0 64 64" fill="none" stroke="#1f2a36" stroke-width="2"><path d="M4 22l28-12 28 12-28 12z" fill="#f4a81c"/><path d="M16 28v14c0 5 32 5 32 0V28"/><path d="M54 25v16"/><path d="M52 41h4l1 8h-6z"/></svg>
  <h3>Our Teaching Team</h3>
  <p>Madame la Préfète des Etudes, Hélène Marchal Madame le Proviseur, Claire Dumonceau Madame Sarah Vandeleene : 081/402210&nbsp;&nbsp; Fax général : 081/402290</p>
  <span class="more">Read More</span>
</div>
<div class="card" style="left:787px;top:766px">
  <svg viewBox="0 0 64 64" fill="none" stroke="#1f2a36" stroke-width="2"><path d="M32 14C24 10 14 10 6 12v40c8-2 18-2 26 2 8-4 18-4 26-2V12c-8-2-18-2-26 2z"/><path d="M32 14v40"/><path d="M12 20h14M12 26h14M12 32h14M12 38h14M38 20h14M38 26h14M38 32h14M38 38h14"/><path d="M2 56h60" stroke="#f4a81c"/></svg>
  <h3>Rules of procedure</h3>
  <p>Veuillez trouvez ci-joint le règlement intérieur:&nbsp; règlement intérieur Veuillez trouvez ci-joint les grilles horaires: Grille d’option 1ère année Grille d’option 2ème année</p>
  <span class="more">Read More</span>
</div>

<h2 class="abs section-title">Students Activites</h2>
<div class="abs rule" style="left:567px;top:1222px;width:46px"></div>

<article>
  <div class="post-img" style="left:89px;background:linear-gradient(170deg,#b9c4cc 0%,#5d7fa6 25%,#8fae6a 55%,#3f6a2a 85%,#7a8a6a 100%)" role="img" aria-label="Photo of three children walking out of school with backpacks"></div>
  <span class="arrow-btn" style="left:482px"><svg width="16" height="12" viewBox="0 0 16 12"><path d="M1 6h13M9 1l5 5-5 5" fill="none" stroke="#1f2a36" stroke-width="1.6"/></svg></span>
  <h4 class="post-date" style="left:90px">18/09/2018</h4>
  <p class="post-text" style="left:91px">Visite du rucher école de la ville de Velmont avec les 6èmes Sciences – génétique et écologie des pollinisateurs</p>
</article>
<article>
  <div class="post-img" style="left:616px;background:linear-gradient(170deg,#e6dcc4 0%,#d2a98a 30%,#b56a5a 55%,#4a7a9a 80%,#2f5f7a 100%)" role="img" aria-label="Photo of smiling young pupils standing together in a classroom"></div>
  <span class="arrow-btn" style="left:1019px"><svg width="16" height="12" viewBox="0 0 16 12"><path d="M1 6h13M9 1l5 5-5 5" fill="none" stroke="#1f2a36" stroke-width="1.6"/></svg></span>
  <h4 class="post-date" style="left:615px">18/09/2018</h4>
  <p class="post-text" style="left:617px">Visite du rucher école de la ville de Velmont avec les 6èmes Sciences – génétique et écologie des pollinisateurs</p>
</article>

<div class="photo" style="left:87px;top:1744px;width:322px;height:210px;background:linear-gradient(180deg,#3f7fd0 0%,#6f9ed8 30%,#6e8aa0 50%,#8a9a5a 68%,#b4b0a4 100%)" role="img" aria-label="Photo of the school building exterior"></div>
<div class="photo" style="left:434px;top:1744px;width:323px;height:210px;background:linear-gradient(180deg,#c9c1a8 0%,#9f8e66 40%,#2f5e86 55%,#c9b586 80%,#b8a57a 100%)" role="img" aria-label="Photo of the school entrance hall"></div>
<div class="photo" style="left:783px;top:1744px;width:321px;height:210px;background:linear-gradient(100deg,#e4e7ea 0%,#cdd3d8 45%,#8a95a4 70%,#3e4c5e 100%)" role="img" aria-label="Photo of a corridor with coat hooks"></div>
<div class="photo" style="left:87px;top:1984px;width:208px;height:211px;background:linear-gradient(160deg,#e2d4b4 0%,#a8845a 45%,#6a5a4a 65%,#e4dccc 100%)" role="img" aria-label="Photo of a kindergarten play corner"></div>
<div class="photo" style="left:323px;top:1984px;width:551px;height:211px;background:linear-gradient(100deg,#8a958e 0%,#aaa79c 35%,#ece8e4 62%,#d8cfc8 75%,#6a4232 100%)" role="img" aria-label="Photo of three girls eating snacks together"></div>
<div class="photo" style="left:897px;top:1984px;width:207px;height:211px;background:linear-gradient(180deg,#f3ecde 0%,#ece0c6 65%,#c88a64 85%,#b57a55 100%)" role="img" aria-label="Photo of an empty classroom"></div>
<div class="photo" style="left:87px;top:2222px;width:322px;height:211px;background:linear-gradient(170deg,#c8303c 0%,#d85a5a 40%,#7a7a9a 65%,#3f6aa6 100%)" role="img" aria-label="Photo of pupils running with schoolbags"></div>
<div class="photo" style="left:434px;top:2222px;width:323px;height:211px;background:linear-gradient(180deg,#c2ae90 0%,#6e6658 40%,#2a2e32 68%,#ecebe8 100%)" role="img" aria-label="Photo of a computer room"></div>
<div class="photo" style="left:783px;top:2222px;width:321px;height:211px;background:linear-gradient(100deg,#3f6fa8 0%,#b8ae98 40%,#c8c2b0 55%,#d2508e 80%,#5e86a8 100%)" role="img" aria-label="Photo of a long school corridor"></div>

<a class="btn orange" style="left:488px;top:2469px;width:223px;height:53px;font-size:15.5px">Our Schedules &amp; Daycare</a>

<div class="abs map" role="img" aria-label="Map showing the school location">
  <svg class="abs" style="left:283px;top:240px" width="46" height="70" viewBox="0 0 46 70"><path d="M23 2a21 21 0 0 0-21 21c0 16 21 45 21 45s21-29 21-45A21 21 0 0 0 23 2z" fill="#c81e2b"/><circle cx="23" cy="22" r="8" fill="#fff"/></svg>
</div>

<section class="abs contact">
  <h2>Contact Us</h2>
  <div class="abs rule" style="left:66px;top:137px;width:38px;background:#fff"></div>
  <div class="field" style="left:66px;top:188px;width:188px">Your Name</div>
  <div class="field" style="left:277px;top:188px;width:189px">Your Email</div>
  <div class="field" style="left:66px;top:249px;width:188px">Phone</div>
  <div class="field" style="left:277px;top:249px;width:189px">Website</div>
  <div class="field" style="left:66px;top:312px;width:400px;height:63px">Your Message</div>
  <a class="btn orange" style="left:66px;top:416px;width:170px;height:42px;font-size:14.5px">Send Message</a>
</section>

<footer class="abs footer">
  <div class="footer-brand"><span class="mark"></span>Lycée Royal de Velmont</div>
  <p class="flink" style="left:91px;top:126px;font-size:13px;line-height:20px;width:200px;white-space:normal">Lorem ipsum dolor sit amet, consectetur adipiscing elit.</p>
  <span class="flink" style="left:352px;top:66px">News</span>
  <span class="flink" style="left:352px;top:98px">Team</span>
  <span class="flink" style="left:352px;top:130px">Hours and daycare</span>
  <span class="flink" style="left:352px;top:162px">Leave</span>
  <span class="flink" style="left:352px;top:194px">Settlement</span>
  <span class="flink" style="left:546px;top:66px">Communications</span>
  <span class="flink" style="left:546px;top:98px">Activities</span>
  <span class="flink" style="left:546px;top:130px">Careers</span>
  <span class="flink" style="left:546px;top:162px">Contact Us</span>
  <span class="abs" style="left:701px;top:66px;font-size:18px;font-weight:500;color:var(--navy)">Subscribe Now</span>
  <div class="abs rule" style="left:702px;top:100px;width:26px"></div>
  <span class="abs" style="left:701px;top:118px;font-size:17px;color:#8a8f96;white-space:nowrap">Nemo enim ipsam voluptatem quia vol</span>
  <div class="abs" style="left:702px;top:153px;width:283px;height:33px;border:1px solid #dcdcdc;background:#fff;font-size:14px;color:#9a9fa6;padding:7px 16px">Enter Your Email</div>
  <a class="btn orange" style="left:995px;top:153px;width:111px;height:33px;font-size:14.5px;font-family:'Poppins',sans-serif">Subscribe</a>
  <span class="flink" style="left:94px;top:270px;font-size:12.5px">© 2019 All Rights Reserved.</span>
</footer>
<span class="social" style="left:997px" aria-label="Social link"></span>
<span class="social" style="left:1024px" aria-label="Social link"></span>
<span class="social" style="left:1053px" aria-label="Social link"></span>
<span class="social" style="left:1083px" aria-label="Social link"></span>

</body>
</html>
```